New Year's card HTML

can you produce a best new years wishes 2018 design in HTML for our website as what I would like to send by email towards my network of candidates / customers ...

It must be wow, inspiring , design, meaningfull... MMM those people care about me, or those people will help me to go the extra mile, to help me to achieve my career goals, Your best move, enhance my possibilities, bring the love back

Target Market(s)

CEo's / CMO's/ HRDirectors network of 450k

Coding

Coded - Design and coding required

Number of Pages Required

1 page

Colors

Designer to choose colors to be used in the design.

Requirements
Must have
• Logo / visual / website adress www.moravintel.com and a call to action
Should not have
• no sound as our business is confidential

```html
<!DOCTYPE html>
<html lang="en">
<head>
<meta charset="utf-8">
<title>Moravintel – Happy New Year 2018</title>
<link rel="stylesheet" href="https://fonts.googleapis.com/css2?family=Roboto+Condensed:wght@400;700&display=swap">
<style>
  :root {
    --night: #1a1c2c;
    --night-glow: #2a2d40;
    --frame: #ffffff;
    --cream-gold: #f4dba5;
    --gold: #e0a32a;
    --gold-deep: #b87a1c;
    --gold-light: #f1c766;
    --paper: #e9e9e9;
    --white: #ffffff;
  }
  * { margin: 0; padding: 0; box-sizing: border-box; }
  html, body {
    width: 1200px;
    height: 1200px;
    overflow: hidden;
    background: var(--night);
  }
  .card {
    position: relative;
    width: 1200px;
    height: 1200px;
    overflow: hidden;
    background: radial-gradient(ellipse at 50% 45%, var(--night-glow) 0%, var(--night) 70%);
    font-family: "Roboto Condensed", "Arial Narrow", sans-serif;
  }
  .frame {
    position: absolute;
    left: 94px;
    top: 90px;
    width: 1012px;
    height: 1014px;
    border: 7px solid var(--frame);
  }
  .brand {
    position: absolute;
    top: 172px;
    left: 0;
    width: 100%;
    display: flex;
    justify-content: center;
    align-items: center;
    gap: 22px;
    color: var(--white);
  }
  .brand-dot {
    width: 30px;
    height: 30px;
    border-radius: 50%;
    background: var(--white);
  }
  .brand-name {
    font-weight: 400;
    font-size: 62px;
    letter-spacing: 3px;
    line-height: 1;
  }
  .greeting {
    position: absolute;
    top: 396px;
    left: 0;
    width: 100%;
    text-align: center;
    color: var(--cream-gold);
    font-weight: 400;
    font-size: 86px;
    line-height: 1;
  }
  .year {
    position: absolute;
    top: 494px;
    left: 0;
    width: 100%;
    text-align: center;
    color: var(--white);
    font-weight: 700;
    font-size: 296px;
    line-height: 1;
    letter-spacing: -2px;
    -webkit-text-stroke: 3px var(--gold);
    paint-order: stroke fill;
    text-shadow: -7px 7px 0 var(--cream-gold);
  }
  .cta {
    position: absolute;
    left: 438px;
    top: 932px;
    width: 324px;
    height: 92px;
    border-radius: 46px;
    display: flex;
    align-items: center;
    justify-content: center;
    background: linear-gradient(180deg, var(--gold-light) 0%, var(--gold) 55%, var(--gold-deep) 100%);
    color: var(--white);
    font-size: 44px;
    font-weight: 400;
    text-decoration: none;
    box-shadow: 0 4px 10px rgba(0,0,0,0.35);
  }
  .site-address {
    position: absolute;
    top: 1046px;
    left: 0;
    width: 100%;
    text-align: center;
    color: var(--cream-gold);
    font-size: 24px;
    letter-spacing: 1px;
    line-height: 1;
  }
  .decor {
    position: absolute;
  }
  .decor-gifts-top {
    left: 0;
    top: 0;
    width: 360px;
    height: 130px;
    background: linear-gradient(90deg, var(--paper) 0%, var(--gold-light) 50%, var(--paper) 100%);
  }
  .decor-disco-ball {
    left: 974px;
    top: 50px;
    width: 164px;
    height: 164px;
    background: linear-gradient(135deg, var(--gold-light) 0%, var(--gold-deep) 100%);
  }
  .decor-gift-right {
    left: 952px;
    top: 826px;
    width: 210px;
    height: 200px;
    background: linear-gradient(135deg, var(--paper) 0%, var(--gold-light) 100%);
  }
  .decor-star {
    left: 0;
    top: 1000px;
    width: 210px;
    height: 200px;
    background: linear-gradient(135deg, var(--gold-light) 0%, var(--gold-deep) 100%);
  }
</style>
</head>
<body>
  <main class="card">
    <div class="frame"></div>

    <div class="decor decor-gifts-top" role="img" aria-label="Wrapped gift boxes with gold bows and a string of gold beads"></div>
    <div class="decor decor-disco-ball" role="img" aria-label="Gold mirror disco ball"></div>

    <div class="brand">
      <span class="brand-dot"></span>
      <span class="brand-name">MORAVINTEL</span>
    </div>

    <h1 class="greeting">Happy New Year</h1>
    <p class="year">2018</p>

    <a class="cta" href="https://www.moravintel.com">Visit Our Site</a>
    <p class="site-address">www.moravintel.com</p>

    <div class="decor decor-gift-right" role="img" aria-label="Polka-dot gift box tied with a gold ribbon bow"></div>
    <div class="decor decor-star" role="img" aria-label="Shiny gold star ornament"></div>
  </main>
</body>
</html>
```